Stylish business cards for KV7

To create an appealing and professional business card design for a WOMEN Owned Construction Supply Company.
2 sided card. Incorporate brand elements, curvy, colorful, sleek and bright. No solid white background. attached samples of styles added shapes/ribbons. Want something with that WOW that looks awesome, factor. It is a new logo, so feel free to mess with logo colors in the blue and teal factors that can look good with both dark and light background. If you want to try a watermark with just the KV7, without the "Supply" that might look cool to.

Industry/Entity Type

Women owned construction supply company

Contact Information for Business Card

Name, Title, and phone number and email, web page. maybe spot for qr code.

Font styles to use
Sans Serif

Requirements
Nice to have
• would love to see colors, maybe stylish ribbon dividers or some sort of 2 or 3 tone color card that compliments logo.
Should not have
• Please do not have all white background. Do not include Home/reale state/ or building images.

```html
<!DOCTYPE html>
<html lang="en">
<head>
<meta charset="utf-8">
<title>KV7 Supply – Business Cards</title>
<link href="https://fonts.googleapis.com/css2?family=Poppins:wght@400;500;600&display=swap" rel="stylesheet">
<style>
  :root{
    --stage:#2b2b2d;
    --navy:#1f3a5c;
    --navy-deep:#172c47;
    --blue:#2f5f8f;
    --teal:#2a9ec9;
    --teal-light:#5cc4e0;
    --silver:#d6d9de;
    --ink:#4a4a4a;
    --paper-top:#f4f8fb;
    --paper-bottom:#e3eef5;
  }
  *{box-sizing:border-box;margin:0;padding:0}
  html,body{width:1200px;height:875px;overflow:hidden}
  body{
    background:var(--stage);
    font-family:"Poppins",sans-serif;
    position:relative;
  }
  .card{
    position:absolute;
    width:540px;height:309px;
    border-radius:22px;
    overflow:hidden;
  }
  .card--front{left:40px;top:120px;background:linear-gradient(135deg,var(--navy) 0%,var(--navy-deep) 100%)}
  .card--back{left:620px;top:446px;background:linear-gradient(160deg,var(--paper-top) 0%,var(--paper-bottom) 100%)}

  .ribbons{position:absolute;left:0;top:0;width:540px;height:309px}

  .front-wordmark{
    position:absolute;left:0;right:0;top:92px;
    text-align:center;
    color:var(--silver);
    font-weight:500;
    font-size:54px;
    line-height:1.2;
    letter-spacing:2px;
  }

  .back-wordmark{
    position:absolute;right:44px;top:34px;
    color:var(--navy);
    font-weight:600;
    font-size:104px;
    line-height:1;
    letter-spacing:-1px;
  }
  .back-rule{position:absolute;left:300px;top:150px;width:240px;height:4px;background:var(--teal)}

  .contact{position:absolute;left:40px;bottom:34px;color:var(--ink);font-size:12px;line-height:1.45}
  .contact__name{color:var(--teal);font-weight:600;font-size:18px;letter-spacing:.5px;line-height:1.1}
  .contact__title{font-size:13px;margin-bottom:10px}
  .contact__address{margin-bottom:10px}
  .contact__row{display:flex;align-items:center;gap:8px}
  .contact__row svg{width:11px;height:11px;fill:var(--teal);flex:none}
</style>
</head>
<body>
  <section class="card card--front" aria-label="Card front">
    <svg class="ribbons" viewBox="0 0 540 309" aria-hidden="true">
      <path d="M0 270 C140 235 300 300 540 220 L540 309 L0 309 Z" fill="var(--blue)" opacity=".55"/>
      <path d="M0 292 C170 255 330 305 540 248 L540 262 C330 318 170 270 0 306 Z" fill="var(--teal)"/>
      <path d="M200 309 C320 280 430 300 540 275 L540 309 Z" fill="var(--teal-light)" opacity=".35"/>
    </svg>
    <div class="front-wordmark">KV7 Supply</div>
  </section>

  <section class="card card--back" aria-label="Card back">
    <svg class="ribbons" viewBox="0 0 540 309" aria-hidden="true">
      <path d="M250 309 C340 270 440 280 540 200 L540 309 Z" fill="var(--navy)"/>
      <path d="M230 309 C330 258 430 262 540 178 L540 194 C440 276 345 276 262 309 Z" fill="var(--teal)"/>
      <path d="M360 309 C420 292 480 282 540 250 L540 309 Z" fill="var(--blue)" opacity=".7"/>
    </svg>
    <div class="back-wordmark">KV7</div>
    <div class="back-rule"></div>

    <div class="contact">
      <div class="contact__name">DANIEL BROOKS</div>
      <div class="contact__title">General Manager</div>
      <div class="contact__address">42 Harbor Point Drive<br>Easton, PA 18042 USA</div>
      <div class="contact__row">
        <svg viewBox="0 0 24 24" aria-hidden="true"><path d="M6.6 10.8a15 15 0 0 0 6.6 6.6l2.2-2.2a1 1 0 0 1 1-.25 11.4 11.4 0 0 0 3.6.57 1 1 0 0 1 1 1V20a1 1 0 0 1-1 1A17 17 0 0 1 3 4a1 1 0 0 1 1-1h3.5a1 1 0 0 1 1 1c0 1.25.2 2.45.57 3.6a1 1 0 0 1-.25 1z"/></svg>
        <span>+1.555.010.234</span>
      </div>
      <div class="contact__row">
        <svg viewBox="0 0 24 24" aria-hidden="true"><path d="M2 5h20v14H2z M2 5l10 8 10-8"/></svg>
        <span>name@kv7supply.com</span>
      </div>
      <div class="contact__row">
        <svg viewBox="0 0 24 24" aria-hidden="true"><circle cx="12" cy="12" r="10"/></svg>
        <span>www.kv7supply.com</span>
      </div>
    </div>
  </section>
</body>
</html>
```